Need Business Card for our Real Estate Business with Sales Executive's Picture

PANTONE 484 C ( RED)

PANTONE 2766 C ( BLUE

Industry/Entity Type

Real Estate

Contact Information for Business Card

Name, Mobile, email, & picture of Person
Agency Phone, address, Web address

Requirements
Must have
• Our Logo Colours, Agent Picture,

```html
<!DOCTYPE html>
<html lang="en">
<head>
<meta charset="utf-8">
<title>Meridian Real Estate – Business Card</title>
<link href="https://fonts.googleapis.com/css2?family=Fira+Sans:wght@400;500&display=swap" rel="stylesheet">
<style>
  :root {
    --page-bg: #dcd6cf;
    --card-bg: #f4efe9;
    --card-bg-deep: #ebe3da;
    --navy: #1f2a4e;
    --red: #9b2423;
    --ink: #2b2b2b;
    --band-text: #f1dcdc;
    --photo-light: #d9cfc4;
    --photo-mid: #a79a8c;
    --photo-suit: #1d2744;
  }
  * { margin: 0; padding: 0; box-sizing: border-box; }
  html, body { width: 1200px; height: 1054px; overflow: hidden; }
  body {
    background: var(--page-bg);
    font-family: "Fira Sans", Arial, sans-serif;
    position: relative;
  }
  .card {
    position: absolute;
    left: 100px; top: 227px;
    width: 1000px; height: 600px;
    background: linear-gradient(120deg, var(--card-bg) 0%, var(--card-bg-deep) 100%);
    box-shadow: 0 12px 30px rgba(0,0,0,0.18);
    overflow: hidden;
  }
  .agent-photo {
    position: absolute;
    left: 0; bottom: 0;
    width: 440px; height: 600px;
    background:
      linear-gradient(180deg, transparent 55%, var(--photo-suit) 100%),
      radial-gradient(ellipse at 48% 45%, var(--photo-mid) 0%, var(--photo-light) 60%, transparent 100%);
  }
  .brand {
    position: absolute;
    left: 560px; top: 92px;
    display: flex; align-items: center; gap: 16px;
    color: var(--navy);
    font-weight: 500;
    font-size: 40px;
    letter-spacing: 3px;
  }
  .brand-mark {
    width: 22px; height: 22px;
    background: var(--red);
  }
  .agent-name {
    position: absolute;
    left: 528px; top: 220px;
    color: var(--navy);
    font-weight: 500;
    font-size: 34px;
  }
  .agent-title {
    position: absolute;
    left: 528px; top: 268px;
    color: var(--red);
    font-size: 25px;
  }
  .address {
    position: absolute;
    left: 528px; top: 328px;
    color: var(--ink);
    font-size: 24px;
    line-height: 33px;
  }
  .contacts {
    position: absolute;
    left: 528px; top: 420px;
    list-style: none;
    color: var(--ink);
    font-size: 24px;
  }
  .contacts li {
    display: flex; align-items: center; gap: 18px;
    height: 33px;
  }
  .contacts svg { width: 20px; height: 20px; fill: var(--red); flex: none; }
  .web-band {
    position: absolute;
    left: 430px; right: 0; bottom: 0;
    height: 62px;
    background: var(--red);
    color: var(--band-text);
    font-size: 23px;
    line-height: 62px;
    padding-left: 98px;
  }
</style>
</head>
<body>
  <main class="card">
    <div class="agent-photo" role="img" aria-label="Portrait photo of the sales executive in a navy suit"></div>

    <div class="brand">
      <span class="brand-mark"></span>
      <span class="brand-name">MERIDIAN REAL ESTATE</span>
    </div>

    <h1 class="agent-name">Dana Whitfield</h1>
    <p class="agent-title">Managing Director</p>

    <p class="address">415 Alder Ave #2210,<br>Brookfield, CO 80512</p>

    <ul class="contacts">
      <li>
        <svg viewBox="0 0 20 20" aria-hidden="true"><path d="M6 1h8a2 2 0 0 1 2 2v14a2 2 0 0 1-2 2H6a2 2 0 0 1-2-2V3a2 2 0 0 1 2-2zm0 3v10h8V4zm4 11.5a1.2 1.2 0 1 0 0 2.4 1.2 1.2 0 0 0 0-2.4z"/></svg>
        <span>555.214.3870</span>
      </li>
      <li>
        <svg viewBox="0 0 20 20" aria-hidden="true"><path d="M2 7c0-2 3-4 8-4s8 2 8 4v2h-4V7.5c-1-.5-2.5-.8-4-.8s-3 .3-4 .8V9H2zm3 3h10l2 7H3zm5 1.8a2.2 2.2 0 1 0 0 4.4 2.2 2.2 0 0 0 0-4.4z"/></svg>
        <span>555-630-4192</span>
      </li>
      <li>
        <svg viewBox="0 0 20 20" aria-hidden="true"><path d="M1 4h18v12H1zm1.5 1.5v.4L10 11l7.5-5.1v-.4z"/></svg>
        <span>dwhitfield@meridianrealestate.com</span>
      </li>
    </ul>

    <footer class="web-band">www.meridianrealestate.com</footer>
  </main>
</body>
</html>
```